Business Card For Halvenmoor Financial Consulting

Hi, I would like a business card designed. Bold, modern.
Please use the same design as the logo. I have also attached the website design to see the overall theme.
Wordmark Font
Color: Hex: #01AEF7

```html
<!DOCTYPE html>
<html lang="en">
<head>
<meta charset="utf-8">
<title>Halvenmoor Financial Consulting – Business Card</title>
<link href="https://fonts.googleapis.com/css2?family=Noto+Sans:wght@400;600;700&display=swap" rel="stylesheet">
<style>
  :root {
    --backdrop: #e4e4e4;
    --navy: #15232b;
    --navy-deep: #0e191f;
    --brand-blue: #01aef7;
    --name-blue: #2ea3dc;
    --paper: #f4f4f4;
    --ink: #1d2a32;
    --silver: #9aa6ad;
  }
  * { margin: 0; padding: 0; box-sizing: border-box; }
  html, body {
    width: 1200px; height: 960px; overflow: hidden;
    background: var(--backdrop);
    font-family: "Noto Sans", Arial, sans-serif;
  }
  .canvas { position: relative; width: 1200px; height: 960px; }

  .card { position: absolute; left: 297px; width: 606px; height: 346px; overflow: hidden; }

  /* Front */
  .card-front { top: 110px; background: var(--navy); }
  .front-texture {
    position: absolute; inset: 0;
    background: linear-gradient(100deg, #5d6a72 0%, #33424b 28%, #18262e 55%, var(--navy-deep) 100%);
  }
  .front-wordmark {
    position: absolute; right: 14px; top: 215px;
    display: flex; align-items: center; gap: 12px;
  }
  .wordmark-square { width: 46px; height: 46px; border: 4px solid #ffffff; }
  .front-wordmark .wordmark-text {
    color: #ffffff; font-weight: 700; line-height: 1.05;
    text-transform: uppercase;
  }
  .wordmark-main { display: block; font-size: 33px; letter-spacing: 1px; }
  .wordmark-sub { display: block; font-size: 12.5px; letter-spacing: 3.3px; margin-top: 4px; }

  /* Back */
  .card-back { top: 510px; background: var(--paper); }
  .back-wordmark {
    position: absolute; left: 37px; top: 38px;
    display: flex; align-items: center; gap: 10px;
  }
  .back-wordmark .wordmark-square { width: 44px; height: 44px; border-color: var(--navy); border-width: 4px; }
  .back-wordmark .wordmark-text {
    color: var(--navy); font-weight: 700; line-height: 1.05; text-transform: uppercase;
  }
  .back-wordmark .wordmark-main { font-size: 29px; }
  .back-wordmark .wordmark-sub { font-size: 11px; letter-spacing: 2.9px; }

  .holder-name {
    position: absolute; right: 37px; top: 148px;
    color: var(--name-blue); font-weight: 600; font-size: 19px;
  }
  .holder-rule {
    position: absolute; left: 37px; top: 187px; width: 460px; height: 1.5px;
    background: var(--ink);
  }
  .holder-title {
    position: absolute; right: 37px; top: 174px;
    color: var(--ink); font-size: 14.5px;
  }
  .contact-list { position: absolute; left: 37px; top: 206px; list-style: none; }
  .contact-item {
    display: flex; align-items: flex-start; gap: 6px;
    color: var(--ink); font-size: 14.5px; line-height: 20px; margin-bottom: 6px;
  }
  .contact-item svg { width: 14px; height: 14px; margin-top: 3px; flex: none; }
  .back-band {
    position: absolute; left: 0; right: 0; bottom: 0; height: 10px; background: var(--navy);
  }
</style>
</head>
<body>
<main class="canvas">

  <section class="card card-front" aria-label="Card front">
    <div class="front-texture" role="img" aria-label="Dark tonal background pattern fading from silver to navy"></div>
    <div class="front-wordmark">
      <span class="wordmark-square"></span>
      <span class="wordmark-text">
        <span class="wordmark-main">Halvenmoor</span>
        <span class="wordmark-sub">Financial Consulting</span>
      </span>
    </div>
  </section>

  <section class="card card-back" aria-label="Card back">
    <div class="back-wordmark">
      <span class="wordmark-square"></span>
      <span class="wordmark-text">
        <span class="wordmark-main">Halvenmoor</span>
        <span class="wordmark-sub">Financial Consulting</span>
      </span>
    </div>

    <p class="holder-name">Daniel Whitcombe</p>
    <div class="holder-rule"></div>
    <p class="holder-title">President</p>

    <ul class="contact-list">
      <li class="contact-item">
        <svg viewBox="0 0 14 14" fill="none" stroke="#2ea3dc" stroke-width="1.4"><path d="M7 13s4.5-4.4 4.5-7.5a4.5 4.5 0 0 0-9 0C2.5 8.6 7 13 7 13z"/><circle cx="7" cy="5.5" r="1.6"/></svg>
        <span>418 Larkspur Avenue, Suite 210<br>Brookfield, CA 95012</span>
      </li>
      <li class="contact-item">
        <svg viewBox="0 0 14 14" fill="none" stroke="#2ea3dc" stroke-width="1.4"><path d="M3 1.5l2.2 2.6-1.3 1.6c.8 1.7 2.1 3 3.8 3.8l1.6-1.3 2.6 2.2-1.4 1.8C6 11.7 2.3 8 1.2 2.9z"/></svg>
        <span>555-014-2278</span>
      </li>
      <li class="contact-item">
        <svg viewBox="0 0 14 14" fill="none" stroke="#2ea3dc" stroke-width="1.4"><rect x="1" y="2.5" width="12" height="9"/><path d="M1 3l6 4.5L13 3"/></svg>
        <span>daniel@halvenmoor.com</span>
      </li>
      <li class="contact-item">
        <svg viewBox="0 0 14 14" fill="none" stroke="#2ea3dc" stroke-width="1.2"><circle cx="7" cy="7" r="5.8"/><ellipse cx="7" cy="7" rx="2.5" ry="5.8"/><path d="M1.2 7h11.6M2 4h10M2 10h10"/></svg>
        <span>www.halvenmoor.com</span>
      </li>
    </ul>

    <div class="back-band"></div>
  </section>

</main>
</body>
</html>
```